Bold, Modern, Clean "Kestrelwaymassage.com" website

Why we stand out?
We are a male and female mobile massage team. Our names are Paul and Lina. 
Kestrel Way is a Seattle based mobile massage service. Our massage is offered to the community with a goal of facilitating balance within each individual. We specialize in integrated Pain management, and sports/medical massage therapy. Every client's first assessment is attended by our male and female massage therapist team. Depending on the goals identified for an individual determines which therapist will be assigned to provide treatment, if not both.

Our passion...
Here at Kestrel Way, we have a great passion for Postural Resoration and how it is integrated into an individual's Massage treatment. We pride ourselves in being natural facilitators of healing, which takes the ego of the therapist out of the client's healing process. We strive to deliver the best massage possible by including modalities such as Neuromuscular, Myofascial release, spontaneous muscle release, postural restoration, orthopedic, and medical massage.

Our education...

We are both Graduates of Venmora, school of massage therapy. We have continuing education in medical massage, myofacial release, trigger point therapy, postural restoration, anatomy, and spontaneous muscle release. Lina is also a Certified Yoga Instructor, which amplifies her experience with flexibility and strength as it pertains to each individual. Paul's passion is Massage, stretching, and strength training to encourage postural restoration and realignment.

Our rates-

Our rates are $75/ 60 minutes, $95/ 90 minutes, and $120/ 120 minutes.

Education-
Both Lina and I worked as behavioral health professionals that specialized in life skills mentoring for youth who had experienced different types of trauma. This led us both to want to help others in a different environment, where individuals can be empowered to take responsibility over their own healing. To us, massage is a type of manipulation physical therapy, that encourages healing on many levels.

Advice to any massage client-
The most important thing to 'us', as Licenced providers is to get you on to our table to show you our skills. But a good therapist never forgets that it's not about what we do for you, but what we can facilitate for you. Your health and healing has nothing to do with us. It is yours, not ours. Identify what your goals are with any Therapist, and know what the end looks like. Progress should be tangible, such as range of motion, and decreased pain.

Lina and Paul at Kestrel Way are awesome! I recently had open heart surgery, and Lina worked on me to increase my range of motion while helping with the pinched nerve from my arm being in the same position for so long during my surgery. My wife drives a lot for work, and Paul has helped decrease her neck and lower back pain immensely. They are seriously the best therapists I have ever worked with. I would recommend them to anyone who needs anything from stress relief to a medical massage treatment. They are professional, up beat, easy going, and always on time. And, I love that they meet us where ever we like! We did a staycation recently, where they came to our hotel to give us relaxation massages. Although usually they come to our home, where we focus on pain related issues. We will continue to work with them for a long, long time.

Target Market(s)

Mobile massage therapy clients

Industry/Entity Type

Massage Therapy

Coding

Coded - Design and coding required

Number of Pages Required

1 page

Font styles to use
Serif
Sans Serif

Requirements
Must have
• Please add or remove any information that would help the presentation of our website. Our logo is posted below, please include into the website.
• Please include a contact field that includes, kestrelwaymassage@fernmail.net,
• (206) 555-0148
• We have also included our own stock photos, as well as a photo of Paul and Lina. Please include a cropped photo of both massage therapists.

```html
<!DOCTYPE html>
<html lang="en">
<head>
<meta charset="utf-8">
<title>Kestrel Way – Mobile Massage</title>
<link rel="stylesheet" href="https://fonts.googleapis.com/css2?family=Arvo:wght@400;700&family=Lato:wght@400;700&family=Abel&family=Kaushan+Script&display=swap">
<style>
:root{
  --red:#c1504c;
  --red-dark:#a9403c;
  --red-light:#d87a72;
  --blue:#1a22a6;
  --navy:#262262;
  --orange:#e9a06a;
  --ink:#333;
  --muted:#8a8a8a;
  --panel:#f2f2f2;
  --white:#fff;
}
*{margin:0;padding:0;box-sizing:border-box}
html,body{width:1200px;height:2406px;overflow:hidden;background:var(--white)}
body{position:relative;font-family:"Lato",sans-serif;color:var(--ink)}
.abs{position:absolute}

/* top bar */
.inquiry-btn{left:82px;top:18px;width:150px;height:36px;border-radius:18px;background:var(--blue);color:var(--white);font:700 14px "Lato",sans-serif;display:flex;align-items:center;justify-content:center;gap:7px}
.top-contact{right:82px;top:24px;display:flex;gap:28px;font-size:14px;color:var(--ink)}
.top-contact span{display:flex;align-items:center;gap:8px}

/* nav */
.nav{left:0;top:72px;width:1200px;height:56px;background:var(--red)}
.nav::before,.nav::after{content:"";position:absolute;left:0;right:0;border-top:1px dashed rgba(255,255,255,.55)}
.nav::before{top:4px}.nav::after{bottom:4px}
.nav-item{top:0;height:56px;line-height:56px;color:var(--white);font-size:14.5px;letter-spacing:.5px}
.nav-item.active{color:#f6c9a6}
.nav-star{top:0;height:56px;line-height:56px;color:var(--white);font-size:11px}
.brand{left:528px;top:24px;width:144px;height:144px;border-radius:50%;background:var(--blue);border:6px solid var(--white);box-shadow:0 0 0 2px var(--blue);display:flex;align-items:center;justify-content:center;text-align:center;color:var(--white);font:700 24px/1.05 "Lato",sans-serif;z-index:2}

/* hero */
.hero{left:0;top:128px;width:1200px;height:527px;background:linear-gradient(100deg,#5b4a36 0%,#b89878 35%,#e4cdb6 55%,#9b7a5a 80%,#4e5a36 100%)}
.hero-title{left:289px;top:196px;font:400 64px/1 "Kaushan Script",cursive;color:var(--white)}
.hero-title.t2{top:272px;color:var(--orange)}
.hero-sub{left:360px;top:344px;font-size:26px;color:var(--white)}
.hero-rule{left:0;top:655px;width:1200px;height:8px;background:#d4d4d4}

/* section titles */
.sec-title{left:0;width:1200px;text-align:center;font:700 28px "Arvo",serif;color:var(--red)}
.sec-title b{color:var(--blue)}
.divider{left:500px;width:200px;height:20px}

/* about */
.about-lead{left:80px;top:779px;width:1040px;text-align:center;font-size:12.5px;line-height:20px;color:var(--ink)}
.about-visual{left:64px;top:882px;width:490px;height:297px;background:radial-gradient(ellipse at 30% 50%,#d9487a 0%,#e9a7bf 35%,transparent 62%),radial-gradient(ellipse at 70% 45%,#8e8a84 0%,#c9c5bf 40%,transparent 65%),var(--white)}
.feature{left:605px;width:515px;height:100px}
.feature .icon{position:absolute;left:0;top:0;width:82px;height:82px;border-radius:50%;background:var(--red);border:4px solid var(--white);box-shadow:0 0 0 2px #ddd}
.feature h3{position:absolute;left:112px;top:0;font:700 17px "Arvo",serif;color:var(--red)}
.feature p{position:absolute;left:112px;top:28px;width:400px;font-size:11.5px;line-height:20px;color:var(--muted)}
.feature .more{position:absolute;right:0;top:74px;font-size:11px;font-weight:700;color:var(--blue);text-decoration:underline}

/* prices */
.prices{left:0;top:1184px;width:1200px;height:532px;background:var(--panel);border-top:3px solid #ddd;border-bottom:3px solid #ddd}
.card{top:1318px;width:241px;height:355px;background:var(--white);border:1px solid #cfcfcf;padding:5px}
.card-inner{position:relative;height:100%;border:1px solid #e2e2e2;text-align:center}
.card-head{height:128px;background:linear-gradient(var(--red),var(--red-light));color:var(--white);font:400 30px/80px "Abel",sans-serif}
.price{position:absolute;left:60px;top:72px;width:112px;height:112px;border-radius:50%;background:var(--white);border:5px solid #f0e3e2;font:700 36px/102px "Lato",sans-serif;color:var(--blue)}
.card h4{position:absolute;left:0;right:0;top:200px;font:700 19px "Lato",sans-serif;color:var(--blue)}
.card p{position:absolute;left:10px;right:10px;top:230px;font-size:11.5px;line-height:17px;color:#666}
.card .btn{position:absolute;left:61px;top:287px;width:106px;height:34px;line-height:34px;background:var(--red);color:var(--white);font-size:13px}

/* testimonials */
.avatar{left:546px;top:1853px;width:108px;height:108px;border-radius:50%;background:radial-gradient(circle,#b7b9c0,#e6e7ea);border:2px dashed #aaa}
.quote{left:280px;top:1978px;width:700px;text-align:center;font-size:12.5px;line-height:21px;color:var(--ink)}
.quote-mark{left:258px;top:1960px;font:700 50px "Arvo",serif;color:#eed7d5}
.quote-name{left:0;top:2026px;width:1200px;text-align:center;font-size:13px;font-weight:700}
.dots{left:570px;top:2066px;display:flex;gap:12px}
.dots i{width:12px;height:12px;border-radius:50%;background:var(--red)}
.dots i.on{background:var(--navy)}
.deco-left{left:0;top:1990px;width:260px;height:124px;background:linear-gradient(90deg,#8e7fb0,#c8c2d2 50%,rgba(255,255,255,0))}
.deco-right{left:900px;top:1958px;width:300px;height:156px;background:linear-gradient(270deg,#f2f2f2,#e9d9e0 45%,#d7e5b8 70%,rgba(255,255,255,0))}

/* footer */
.footer{left:0;top:2114px;width:1200px;height:257px;background:var(--navy);color:var(--white)}
.f-col{top:40px}
.f-col h5{font:400 17px "Lato",sans-serif;padding-bottom:10px;border-bottom:1px dashed rgba(255,255,255,.35);margin-bottom:12px}
.f-links li{list-style:none;font-size:12.5px;line-height:24px}
.f-links li::before{content:"›";margin-right:10px}
.vsep{top:40px;width:1px;height:180px;background:rgba(255,255,255,.18)}
.field{width:226px;height:24px;background:var(--white);border-radius:3px;color:#555;font-size:12px;padding:4px 8px;margin-bottom:7px}
.field.tall{height:40px}
.submit{width:62px;height:22px;line-height:22px;text-align:center;background:var(--red-light);border-radius:3px;font-size:12px}
.contact-row{display:flex;gap:12px;font-size:12.5px;line-height:18px;margin-bottom:14px}
.f-brand{left:983px;top:39px;width:128px;height:128px;border-radius:50%;background:#4b4a86;border:4px solid #6e6da4;display:flex;align-items:center;justify-content:center;text-align:center;color:#8f8fc2;font:700 21px/1.05 "Lato",sans-serif}
.social{top:190px;width:32px;height:32px;border-radius:50%}
.bottom-bar{left:0;top:2371px;width:1200px;height:35px;background:var(--red);color:var(--white);font-size:11.5px;line-height:35px}
</style>
</head>
<body>

<!-- top bar -->
<div class="abs inquiry-btn">
  <svg width="13" height="13" viewBox="0 0 13 13"><rect x="1" y="2" width="11" height="10" rx="1" fill="none" stroke="#fff" stroke-width="1.4"/><line x1="1" y1="5" x2="12" y2="5" stroke="#fff" stroke-width="1.4"/></svg>
  QUICK INQUERY
</div>
<div class="abs top-contact">
  <span><svg width="15" height="11" viewBox="0 0 15 11"><rect x=".7" y=".7" width="13.6" height="9.6" fill="none" stroke="#1a22a6" stroke-width="1.4"/><path d="M1 1l6.5 5L14 1" fill="none" stroke="#1a22a6" stroke-width="1.4"/></svg>kestrelwaymassage@fernmail.net</span>
  <span><svg width="14" height="14" viewBox="0 0 14 14"><path d="M3 1l2.5 3-1.3 1.7c.8 1.7 2.3 3.2 4 4L9.9 8.4 13 11l-1.6 2.2C6 13 1 8 .8 2.6z" fill="#1a22a6"/></svg>(206) 555-0148</span>
</div>

<!-- navigation -->
<nav class="abs nav">
  <span class="abs nav-item active" style="left:80px">HOME</span>
  <span class="abs nav-star" style="left:169px">★</span>
  <span class="abs nav-item" style="left:218px">ABOUT US</span>
  <span class="abs nav-star" style="left:332px">★</span>
  <span class="abs nav-item" style="left:384px">SERVICES</span>
  <span class="abs nav-star" style="left:496px">★</span>
  <span class="abs nav-star" style="left:694px">★</span>
  <span class="abs nav-item" style="left:728px">PRICES</span>
  <span class="abs nav-star" style="left:803px">★</span>
  <span class="abs nav-item" style="left:838px">PHOTO GALLERY</span>
  <span class="abs nav-star" style="left:988px">★</span>
  <span class="abs nav-item" style="left:1023px">CONTACT US</span>
</nav>
<div class="abs brand">KESTREL<br>WAY</div>

<!-- hero -->
<div class="abs hero" role="img" aria-label="Photo of therapists giving relaxing back massages to clients at a spa"></div>
<div class="abs hero-title">MASSAGE</div>
<div class="abs hero-title t2">THERAPY</div>
<div class="abs hero-sub">We come to you</div>
<div class="abs hero-rule"></div>

<!-- about -->
<h2 class="abs sec-title" style="top:690px">ABOUT <b>US</b></h2>
<svg class="abs divider" style="top:733px" viewBox="0 0 200 20"><line x1="0" y1="8" x2="80" y2="8" stroke="#e3b4a8"/><line x1="0" y1="12" x2="80" y2="12" stroke="#e3b4a8"/><line x1="120" y1="8" x2="200" y2="8" stroke="#e3b4a8"/><line x1="120" y1="12" x2="200" y2="12" stroke="#e3b4a8"/><circle cx="100" cy="10" r="9" fill="#444"/><circle cx="100" cy="10" r="5" fill="none" stroke="#ddd"/></svg>
<p class="abs about-lead">We are a male and female mobile massage team. Our names are Paul and Lina. Kestrel Way is a Seattle based mobile massage service. Our massage is offered to the community with a goal of facilitating balance within each individual. We specialize in integrated Pain management, and sports/medical massage therapy. Every client's first assessment is attended by our male and female massage therapist team. Depending on the goals identified for an individual determines which therapist will be assigned to provide treatment, if not both.</p>

<div class="abs about-visual" role="img" aria-label="Pink daisies and stacked spa stones with scattered petals"></div>

<div class="abs feature" style="top:858px">
  <div class="icon"><svg width="74" height="74" viewBox="0 0 74 74"><rect x="20" y="40" width="34" height="5" fill="#fff"/><circle cx="37" cy="28" r="7" fill="#fff"/></svg></div>
  <h3>Why We Stand Out?</h3>
  <p>Kestrel Way is a Seattle based mobile massage service. Our massage is offered to the community with a goal of facilitating balance within each individual.</p>
  <span class="more">Read More &nbsp;»</span>
</div>
<div class="abs feature" style="top:962px">
  <div class="icon"><svg width="74" height="74" viewBox="0 0 74 74"><circle cx="28" cy="30" r="6" fill="#fff"/><circle cx="46" cy="30" r="6" fill="#fff"/><rect x="20" y="40" width="34" height="6" fill="#fff"/></svg></div>
  <h3>Our Passion.</h3>
  <p>Here at Kestrel Way, we have a great passion for Postural Resoration and how it is integrated into an individual's Massage treatment. We pride ourselves in being natural</p>
  <span class="more">Read More &nbsp;»</span>
</div>
<div class="abs feature" style="top:1067px">
  <div class="icon"><svg width="74" height="74" viewBox="0 0 74 74"><rect x="32" y="22" width="24" height="18" fill="none" stroke="#fff" stroke-width="2.5"/><circle cx="24" cy="34" r="5" fill="#fff"/><rect x="20" y="41" width="8" height="14" fill="#fff"/></svg></div>
  <h3>Our Education.</h3>
  <p>We are both Graduates of Venmora, school of massage therapy. We have continuing education in medical massage, myofacial release, trigger point therapy, postural restoration, anatomy</p>
  <span class="more">Read More &nbsp;»</span>
</div>

<!-- prices -->
<section class="abs prices"></section>
<h2 class="abs sec-title" style="top:1215px">OUR <b>PRICES</b></h2>
<svg class="abs divider" style="top:1261px" viewBox="0 0 200 20"><line x1="0" y1="8" x2="80" y2="8" stroke="#e3b4a8"/><line x1="0" y1="12" x2="80" y2="12" stroke="#e3b4a8"/><line x1="120" y1="8" x2="200" y2="8" stroke="#e3b4a8"/><line x1="120" y1="12" x2="200" y2="12" stroke="#e3b4a8"/><circle cx="100" cy="10" r="9" fill="#444"/><circle cx="100" cy="10" r="5" fill="none" stroke="#ddd"/></svg>

<div class="abs card" style="left:80px"><div class="card-inner"><div class="card-head">60 minutes</div><div class="price">$75</div><h4>MASSAGE THERAPY</h4><p>Both Lina and I worked as behavioral health professionals that specialized in life skills mentoring for</p><div class="btn">Read More</div></div></div>
<div class="abs card" style="left:346px"><div class="card-inner"><div class="card-head">90 minutes</div><div class="price">$95</div><h4>MASSAGE THERAPY</h4><p>Both Lina and I worked as behavioral health professionals that specialized in life skills mentoring for</p><div class="btn">Read More</div></div></div>
<div class="abs card" style="left:613px"><div class="card-inner"><div class="card-head">120 minutes</div><div class="price">$120</div><h4>MASSAGE THERAPY</h4><p>Both Lina and I worked as behavioral health professionals that specialized in life skills mentoring for</p><div class="btn">Read More</div></div></div>
<div class="abs card" style="left:879px"><div class="card-inner"><div class="card-head">150 minutes</div><div class="price">$150</div><h4>MASSAGE THERAPY</h4><p>Both Lina and I worked as behavioral health professionals that specialized in life skills mentoring for</p><div class="btn">Read More</div></div></div>

<!-- testimonials -->
<h2 class="abs sec-title" style="top:1751px">CLIENT <b>TESTIMONIALS</b></h2>
<svg class="abs divider" style="top:1797px" viewBox="0 0 200 20"><line x1="0" y1="8" x2="80" y2="8" stroke="#e3b4a8"/><line x1="0" y1="12" x2="80" y2="12" stroke="#e3b4a8"/><line x1="120" y1="8" x2="200" y2="8" stroke="#e3b4a8"/><line x1="120" y1="12" x2="200" y2="12" stroke="#e3b4a8"/><circle cx="100" cy="10" r="9" fill="#444"/><circle cx="100" cy="10" r="5" fill="none" stroke="#ddd"/></svg>
<div class="abs avatar" role="img" aria-label="Portrait photo of the client giving the testimonial"></div>
<div class="abs deco-left" role="img" aria-label="Rolled lavender towel with spa stones and lavender sprigs"></div>
<div class="abs deco-right" role="img" aria-label="Stacked white towels with candles and a pink lily"></div>
<div class="abs quote-mark">“</div>
<p class="abs quote">The most important thing to 'us', as Licenced providers is to get you on to our table to show you our skills. But a good therapist never forgets that it's not about what we do for you, but what we can facilitate for you.</p>
<div class="abs quote-name">Ms. Nora Delane</div>
<div class="abs dots"><i></i><i class="on"></i><i></i></div>

<!-- footer -->
<footer class="abs footer">
  <div class="abs f-col" style="left:82px;width:126px">
    <h5>Quick Links</h5>
    <ul class="f-links"><li>Home</li><li>About US</li><li>Services</li><li>Prices</li><li>Photo Gallery</li><li>Contact Us</li></ul>
  </div>
  <div class="abs vsep" style="left:255px"></div>
  <div class="abs f-col" style="left:311px;width:226px">
    <h5 style="border:0;margin-bottom:4px">Quick Inquiry</h5>
    <div class="field">Name</div>
    <div class="field">Email</div>
    <div class="field tall">Message</div>
    <div class="submit">Submit</div>
  </div>
  <div class="abs vsep" style="left:589px"></div>
  <div class="abs f-col" style="left:642px;width:236px">
    <h5>Contact Details</h5>
    <div class="contact-row"><svg width="10" height="14" viewBox="0 0 10 14"><path d="M5 0a5 5 0 0 1 5 5c0 3.5-5 9-5 9S0 8.5 0 5a5 5 0 0 1 5-5z" fill="#fff"/><circle cx="5" cy="5" r="2" fill="#262262"/></svg><span>Lorem ipsum dolor sit amet, consectetuer adipiscing elit, sed diam nonummy nibh .</span></div>
    <div class="contact-row"><svg width="12" height="12" viewBox="0 0 14 14"><path d="M3 1l2.5 3-1.3 1.7c.8 1.7 2.3 3.2 4 4L9.9 8.4 13 11l-1.6 2.2C6 13 1 8 .8 2.6z" fill="#fff"/></svg><span>(206) 555-0148</span></div>
    <div class="contact-row"><svg width="13" height="10" viewBox="0 0 15 11"><rect x="0" y="0" width="15" height="11" fill="#fff"/><path d="M1 1l6.5 5L14 1" fill="none" stroke="#262262" stroke-width="1.3"/></svg><span>kestrelwaymassage@fernmail.net</span></div>
  </div>
  <div class="abs vsep" style="left:930px"></div>
  <div class="abs f-brand">KESTREL<br>WAY</div>
  <span class="abs social" style="left:1002px;background:#1e88e5"></span>
  <span class="abs social" style="left:1043px;background:#1e9fd8"></span>
  <span class="abs social" style="left:1083px;background:#e0282c"></span>
</footer>
<div class="abs bottom-bar">
  <span class="abs" style="left:82px">Copyright © 2015 kestrelwaymassage &nbsp;| All Right Reserved.</span>
  <span class="abs" style="left:896px">Terms &amp; Conditions &nbsp;&nbsp;&nbsp; | &nbsp;&nbsp;&nbsp; Privacy Policy</span>
</div>

</body>
</html>
```